Sparrow Haulage needs a business card design.

Design a double-sided business card for new freight business. On the front, would like to see our logo along with the following info:

Martin Obuya
CEO/FOUNDER
555-206-7142
martinobuya@sparrow-haulage.example

On the reverse side, we would like to use the graphic image of our logo only without the Sparrow Haulage name.

```html
<!DOCTYPE html>
<html lang="en">
<head>
<meta charset="utf-8">
<title>Sparrow Haulage — Business Card</title>
<link rel="stylesheet" href="https://fonts.googleapis.com/css2?family=Montserrat:wght@600;700&family=Roboto:wght@400&display=swap">
<style>
  :root {
    --navy: #1b1852;
    --navy-deep: #14113f;
    --red: #c0202e;
    --white: #ffffff;
    --ink-light: #e4e3ee;
    --backdrop: #8c8d8e;
    --pattern-light: #c9c6e0;
    --pattern-mid: #6a66a8;
  }
  * { box-sizing: border-box; margin: 0; padding: 0; }
  html, body {
    width: 1188px; height: 1200px; overflow: hidden;
    background: var(--backdrop);
  }
  .canvas { position: relative; width: 1188px; height: 1200px; }

  .card {
    position: absolute; left: 245px; width: 696px; height: 386px;
    overflow: hidden;
  }
  .card--front { top: 159px; display: flex; }
  .card--back { top: 627px; background: var(--navy); }

  .front__brand {
    width: 331px; height: 100%; background: var(--white);
    display: flex; align-items: center; justify-content: center;
  }
  .brand-name {
    font-family: "Montserrat", sans-serif; font-weight: 700;
    font-size: 22px; line-height: 1.1; letter-spacing: 3px;
    color: var(--navy); text-transform: uppercase;
  }
  .front__info {
    flex: 1; background: var(--navy); padding: 130px 0 0 34px;
  }
  .person-name {
    font-family: "Montserrat", sans-serif; font-weight: 700;
    font-size: 20px; color: var(--red); line-height: 1.2;
  }
  .person-title {
    font-family: "Roboto", sans-serif; font-size: 16px;
    color: var(--ink-light); margin-top: 2px;
  }
  .contact-list { list-style: none; margin-top: 21px; }
  .contact-list li {
    display: flex; align-items: center; gap: 6px;
    font-family: "Roboto", sans-serif; font-size: 16px;
    color: var(--ink-light); height: 21.5px;
  }
  .contact-icon { width: 15px; height: 15px; flex: none; }

  .back__pattern {
    position: absolute; inset: 0;
    background: linear-gradient(100deg, var(--pattern-light) 0%, var(--pattern-mid) 40%, var(--navy) 85%);
    opacity: 0.55;
  }
  .back__wordmark {
    position: absolute; left: 378px; top: 262px;
    padding: 6px 8px; background: var(--navy);
  }
  .back__wordmark .brand-name { color: var(--white); font-size: 22px; }
</style>
</head>
<body>
<main class="canvas">
  <section class="card card--front" aria-label="Business card front">
    <div class="front__brand">
      <p class="brand-name">Sparrow<br>Haulage</p>
    </div>
    <div class="front__info">
      <h1 class="person-name">Martin Obuya</h1>
      <p class="person-title">CEO/FOUNDER</p>
      <ul class="contact-list">
        <li>
          <svg class="contact-icon" viewBox="0 0 16 16" aria-hidden="true"><path fill="#c0202e" d="M3.5 1.5l2.5 0 1 3.5-1.7 1.2c.8 1.8 2.2 3.2 4 4l1.2-1.7 3.5 1v2.5c0 .8-.7 1.5-1.5 1.5C6.8 13.5 2 8.7 2 3c0-.8.7-1.5 1.5-1.5z"/></svg>
          555-206-7142
        </li>
        <li>
          <svg class="contact-icon" viewBox="0 0 16 16" aria-hidden="true"><rect x="1" y="3.5" width="14" height="9" fill="#c0202e"/><path d="M1.5 4l6.5 5 6.5-5" stroke="#1b1852" stroke-width="1.2" fill="none"/></svg>
          martinobuya@sparrow-haulage.example
        </li>
        <li>
          <svg class="contact-icon" viewBox="0 0 16 16" aria-hidden="true"><circle cx="8" cy="8" r="7" fill="#c0202e"/><path d="M4 5c2 0 2 2 4 2s1 3-1 3-1 3-2 3M10 2.5c0 2 2 2 3 3" stroke="#1b1852" stroke-width="1.2" fill="none"/></svg>
          www.sparrow-haulage.example
        </li>
      </ul>
    </div>
  </section>

  <section class="card card--back" aria-label="Business card back">
    <div class="back__pattern" role="img" aria-label="Repeating embossed brand-mark pattern fading from silver on the left to navy on the right"></div>
    <div class="back__wordmark">
      <p class="brand-name">Sparrow<br>Haulage</p>
    </div>
  </section>
</main>
</body>
</html>
```